Satchel & Sundial needs new business card design

I need a new business card design. I'm looking for out-of-the-box design which represents the freedom of being a location independent entrepreneur.
I offer coaching, retreats and trips.
I would like to see designs with and without the photo.
Colors I use are black (#000000), green (#25A796) and brown (#D7C38C)
Website satchelandsundial.example

Target Market(s)

location independent entrepreneurs, digital nomads, people looking to swap the 9 to 5 for a lifestyle business

Industry/Entity Type

Business

Contact Information for Business Card

Dorota Falkner
Your Lifestyle Business Coach, Retreat & Trip Leader
http://satchelandsundial.example
hello@satchelandsundial.example
Live a life you don't need a holiday from

Font styles to use
Serif
Sans Serif

Requirements
Must have
• One side should contain only the logo. I would also consider having the "Live a life you don't need a holiday from" on that side too (depending on how it looks)
• Please show both sides on the designs.

```html
<!DOCTYPE html>
<html lang="en">
<head>
<meta charset="utf-8">
<title>Satchel &amp; Sundial – Business Card</title>
<link rel="stylesheet" href="https://fonts.googleapis.com/css2?family=Bebas+Neue&display=swap">
<style>
  :root {
    --backdrop: #262626;
    --brand-green: #25A796;
    --brand-sand: #D7C38C;
    --brand-black: #1c1a17;
    --ink-white: #ffffff;
  }
  html, body {
    margin: 0;
    padding: 0;
    width: 1200px;
    height: 987px;
    overflow: hidden;
    background: var(--backdrop);
  }
  .stage {
    position: relative;
    width: 1200px;
    height: 987px;
    font-family: "Bebas Neue", "Arial Narrow", sans-serif;
  }
  .card {
    position: absolute;
    left: 293px;
    width: 615px;
    height: 352px;
  }
  .card-front { top: 130px; background: var(--brand-green); color: var(--ink-white); }
  .card-back  { top: 505px; background: var(--brand-sand); color: var(--brand-black); }

  .card-frame {
    position: absolute;
    inset: 12px;
    border: 3px solid currentColor;
  }
  .card-back .card-frame { border-width: 3px; }

  .line {
    position: absolute;
    left: 0;
    right: 0;
    margin: 0;
    text-align: center;
    line-height: 1;
    letter-spacing: 0.01em;
  }
  .social-links { top: 50px; }
  .social-links svg { display: inline-block; }

  .person-name { top: 123px; font-size: 38px; }
  .person-role { font-size: 22px; }
  .person-role.first  { top: 167px; }
  .person-role.second { top: 197px; }
  .contact-details { top: 262px; font-size: 15.5px; }
  .contact-details .divider { margin: 0 6px; }
  .tagline { top: 284px; font-size: 20px; }

  .brand-name {
    top: 150px;
    font-size: 58px;
    letter-spacing: 0.02em;
    color: var(--brand-black);
  }
</style>
</head>
<body>
  <main class="stage">
    <section class="card card-front" aria-label="Card front">
      <div class="card-frame"></div>
      <div class="line social-links" aria-label="Social media links">
        <svg width="90" height="20" viewBox="0 0 90 20" aria-hidden="true">
          <circle cx="9" cy="10" r="8" fill="#ffffff"/>
          <circle cx="45" cy="10" r="8" fill="#ffffff"/>
          <circle cx="81" cy="10" r="8" fill="#ffffff"/>
        </svg>
      </div>
      <h1 class="line person-name">Dorota Falkner</h1>
      <p class="line person-role first">Your Lifestyle Business Coach</p>
      <p class="line person-role second">Retreat &amp; Trip Leader</p>
      <p class="line contact-details">hello@satchelandsundial.example<span class="divider">|</span>www.satchelandsundial.example</p>
      <p class="line tagline">Live a life you don't need a holiday from</p>
    </section>

    <section class="card card-back" aria-label="Card back">
      <div class="card-frame"></div>
      <p class="line brand-name">Satchel &amp; Sundial</p>
    </section>
  </main>
</body>
</html>
```